Web Developer Needs a Business Card Design

I need a personal business card design that represents me as a web developer for potential employers. I would like the background to be a dark color on the front for contrast with my logo and name. The back will have all my information along with a smaller version of the logo. I want something with a modern look and feel, not too conservative. This will be used for potential employers and freelance work.

Industry/Entity Type

Business

Contact Information for Business Card

Front should have my logo and name. The back should have all my personal information which would include: name: Tom Varulek, phone: 570-614-3098, email: tomvarulek@quillbox.net, website url: www.tomvarulek.net, logo, web developer.

Font styles to use
Sans Serif

Requirements
Must have
• Must include my logo. The color palette base color will be the logo color.

```html
<!DOCTYPE html>
<html lang="en">
<head>
<meta charset="utf-8">
<title>Tom Varulek – Business Card</title>
<link rel="stylesheet" href="https://fonts.googleapis.com/css2?family=Open+Sans:wght@400;600;700&display=swap">
<style>
  :root {
    --teal: #6fcbb7;
    --teal-deep: #4fb39d;
    --ink: #1c1c1c;
    --black-card: #0b0b0b;
    --white-card: #ffffff;
    --silver: #cfd3d4;
    --backdrop: #e9e7e3;
    --muted: #444444;
  }
  * { box-sizing: border-box; margin: 0; padding: 0; }
  html, body { width: 1200px; height: 913px; overflow: hidden; }
  body {
    background: var(--backdrop);
    font-family: "Open Sans", Arial, sans-serif;
    display: flex;
    align-items: center;
    justify-content: center;
    gap: 40px;
  }
  .card {
    position: relative;
    width: 540px;
    height: 309px;
    border-radius: 18px;
    overflow: hidden;
    box-shadow: 0 10px 28px rgba(0,0,0,.18);
  }
  .card-wave { position: absolute; inset: 0; width: 100%; height: 100%; }

  /* Back: contact side */
  .card-back { background: var(--white-card); }
  .back-mark {
    position: absolute; left: 40px; top: 58px; width: 200px;
    display: flex; flex-direction: column; align-items: center; gap: 14px;
  }
  .mark-circle {
    width: 110px; height: 110px; border-radius: 50%;
    border: 12px solid var(--teal);
  }
  .mark-name {
    color: var(--teal); font-weight: 700; font-size: 20px; letter-spacing: .5px;
  }
  .back-divider {
    position: absolute; left: 268px; top: 46px; width: 1px; height: 150px;
    background: linear-gradient(var(--white-card), #9a9a9a, var(--white-card));
  }
  .contact {
    position: absolute; left: 290px; top: 58px; color: var(--ink);
  }
  .contact-name { font-weight: 700; font-size: 20px; letter-spacing: .4px; line-height: 1.1; }
  .contact-role {
    color: var(--teal); font-weight: 600; font-size: 12px; letter-spacing: 1.2px;
    margin-bottom: 12px;
  }
  .contact-list { list-style: none; font-size: 13px; color: var(--muted); }
  .contact-list li { display: flex; align-items: center; gap: 8px; line-height: 21px; }
  .contact-list svg { width: 12px; height: 12px; flex: none; }

  /* Front: dark side */
  .card-front { background: linear-gradient(160deg, #1b1b1b, var(--black-card) 55%); }
  .front-mark {
    position: absolute; left: 0; right: 0; top: 30px;
    display: flex; flex-direction: column; align-items: center; gap: 8px;
  }
  .front-mark .mark-circle { width: 80px; height: 80px; border-width: 9px; }
  .front-name {
    position: absolute; left: 0; right: 0; top: 142px; text-align: center;
    color: #f4f4f4; font-size: 32px; letter-spacing: 3px; font-weight: 400;
  }
  .front-role {
    position: absolute; left: 0; right: 0; top: 190px; text-align: center;
    color: #e6e6e6; font-size: 16px; letter-spacing: .8px;
  }
</style>
</head>
<body>

  <section class="card card-back" aria-label="Card back with contact details">
    <svg class="card-wave" viewBox="0 0 540 309" aria-hidden="true">
      <path d="M0 309 L0 302 Q300 300 540 210 L540 309 Z" fill="var(--teal)"/>
      <path d="M150 296 Q360 282 540 204" fill="none" stroke="#111" stroke-width="4" stroke-linecap="round"/>
    </svg>
    <div class="back-mark">
      <div class="mark-circle"></div>
      <div class="mark-name">Tom Varulek</div>
    </div>
    <div class="back-divider"></div>
    <div class="contact">
      <div class="contact-name">TOM VARULEK</div>
      <div class="contact-role">WEB DEVELOPER</div>
      <ul class="contact-list">
        <li>
          <svg viewBox="0 0 24 24"><path fill="var(--teal)" d="M6.6 10.8a15 15 0 0 0 6.6 6.6l2.2-2.2a1 1 0 0 1 1-.25 11.4 11.4 0 0 0 3.6.57 1 1 0 0 1 1 1V20a1 1 0 0 1-1 1A17 17 0 0 1 3 4a1 1 0 0 1 1-1h3.5a1 1 0 0 1 1 1c0 1.25.2 2.45.57 3.6a1 1 0 0 1-.25 1z"/></svg>
          570-614-3098
        </li>
        <li>
          <svg viewBox="0 0 24 24"><rect x="2" y="5" width="20" height="14" rx="2" fill="none" stroke="var(--teal)" stroke-width="2.4"/><path d="M3 6l9 7 9-7" fill="none" stroke="var(--teal)" stroke-width="2.4"/></svg>
          tomvarulek@quillbox.net
        </li>
        <li>
          <svg viewBox="0 0 24 24"><circle cx="12" cy="12" r="10" fill="none" stroke="var(--teal)" stroke-width="2.4"/><path d="M2 12h20M12 2c3 3 3 17 0 20M12 2c-3 3-3 17 0 20" fill="none" stroke="var(--teal)" stroke-width="2"/></svg>
          www.tomvarulek.net
        </li>
      </ul>
    </div>
  </section>

  <section class="card card-front" aria-label="Card front with name">
    <svg class="card-wave" viewBox="0 0 540 309" aria-hidden="true">
      <path d="M0 309 L0 300 Q300 300 540 205 L540 309 Z" fill="var(--teal)"/>
      <path d="M120 292 Q360 278 540 200" fill="none" stroke="var(--silver)" stroke-width="4" stroke-linecap="round"/>
    </svg>
    <div class="front-mark">
      <div class="mark-circle"></div>
    </div>
    <div class="front-name">TOM VARULEK</div>
    <div class="front-role">Front-End Developer</div>
  </section>

</body>
</html>
```